Wordpress Website design partner needed for an Arabic Language Institute for English Speakers

We are an online Arabic Language institute, targeting English Speakers around the world and we provide online courses and private group and one on one classes
We are looking for a total of 5 pages designed.
The Design should be mobile-first, and then provide PC for any differences.
I am looking for a consistent design with a lot of white space and in line with our Logo colours.
Images used should be around the theme of Arabic Language/Islamic in Nature, so please do not use any illustrations or images of animals or human beings except for silhouettes or images without faces visible, such as someone facing other way or below torso or hands etc.
The website will eventually be prepared for Wordpress using Divi.
I will provide a very structured outline of what elements and modules each page should have. Therefore I am looking for someone that has an eye for detail and is precise in executing requirements.
I decided to post on this site because I am looking for a long-term partner that can take care of any of our design needs as they come up.
More details to follow
I will do abit more research tomorrow to suggest sample sites
Updates
Target Market(s)
English speakers that want to learn Arabic for Religous purposes such as understanding the Quran
Industry/Entity Type
Education
Colors
Designer to choose colors to be used in the design.
Requirements
Must have
- Mobile First, and design for PC for changes
- Consistency
- Plenty of White Space
- Colour Palette based on Logo
- Colour and Transparent/White Header for when scrolling
- Big Call to Action buttons with contrasting colors
- A consistent footer for all pages with
- -Social Media Icons
- -Contact us
- -Sitemap
- -Copyright
- -Logo
- Anything with a hashtag (#) beforehand in the Doc file means it should be a module like the modules used in Divi Theme, Please check the following website for an explanation of what each module consists of and some examples of it in use. https://www.pelmorashowcase.net/pelmora-blocks-guide/
Nice to have
- Parallax Effect
Should not have
- illustrations or images of animals or human beings except for silhouettes or images without faces visible, such as someone facing other way or below torso or hands etc.

```html
<!DOCTYPE html>
<html lang="en">
<head>
<meta charset="utf-8">
<title>Al Bayan Arabic Academy</title>
<link href="https://fonts.googleapis.com/css2?family=Montserrat:ital,wght@0,400;0,500;0,600;1,500&display=swap" rel="stylesheet">
<style>
:root{
  --brand:#2b7bab;
  --brand-dark:#23688f;
  --brand-light:#3a98b8;
  --accent:#f7a11a;
  --accent-edge:#fdd27a;
  --ink:#2f2f2f;
  --muted:#555;
  --panel:#efefef;
  --white:#fff;
}
*{margin:0;padding:0;box-sizing:border-box}
html,body{width:1200px;height:5133px;overflow:hidden}
body{position:relative;background:var(--white);font-family:'Montserrat',sans-serif;color:var(--ink)}
.abs{position:absolute}
.btn{position:absolute;background:var(--accent);color:var(--white);border:2px solid var(--accent-edge);display:flex;align-items:center;justify-content:center;font-weight:500}
.site-header{left:0;top:0;width:1200px;height:137px;border-bottom:1px solid #ddd}
.brand{left:86px;top:20px;display:flex;align-items:center;gap:16px}
.brand-mark{width:56px;height:56px;background:var(--brand)}
.brand-name{font-size:20px;font-weight:600;color:var(--brand);letter-spacing:3px;line-height:1.2}
.nav{left:446px;top:62px;display:flex;gap:42px;font-size:18px;color:var(--brand)}
.nav .active{color:#333}
.promo{left:0;top:137px;width:1200px;height:233px;background:linear-gradient(90deg,var(--brand),var(--brand-light))}
.promo h1{position:absolute;left:106px;top:30px;font-size:38px;font-weight:500;color:var(--white)}
.promo p{position:absolute;left:106px;top:96px;width:720px;font-size:15.5px;line-height:36px;color:var(--white)}
.hero{left:0;top:370px;width:1200px;height:554px;background:linear-gradient(180deg,#c9b9a4 0%,#d8c1a0 40%,#8c8f90 70%,#4f6f7f 100%)}
.hero-title{left:0;top:130px;width:1200px;text-align:center;font-size:80px;font-weight:500;color:var(--brand)}
.hero-sub{left:220px;top:238px;width:760px;text-align:center;font-size:24px;line-height:36px;color:#222}
.arrow{top:248px;width:30px;height:30px}
.dots{display:flex;gap:10px}
.dots span{width:10px;height:10px;border-radius:50%;background:var(--white)}
.photo{background:linear-gradient(135deg,#b8894f,#6a3f22 60%,#3a2415)}
.feature{width:300px;text-align:center}
.feature .icon{width:82px;height:82px;border-radius:50%;background:var(--brand);margin:0 auto}
.feature h3{font-size:23px;font-weight:500;color:#333;margin-top:28px}
.feature p{font-size:16px;line-height:30px;color:var(--muted);margin-top:10px}
.band{left:0;width:1200px;background:linear-gradient(180deg,var(--brand),#3784ac)}
.band-head{left:0;width:1200px;text-align:center;color:var(--white)}
.section-title{left:0;width:1200px;text-align:center;font-size:40px;font-weight:500}
.card{left:156px;width:890px;height:172px}
.card .avatar{position:absolute;left:46px;top:28px;width:118px;height:118px;border-radius:50%;background:radial-gradient(circle,#8a7a6e,#4a4440)}
.card .quote{position:absolute;left:200px;top:18px;width:610px;font-size:16px;line-height:32px}
.card .who{position:absolute;left:200px;top:94px;font-size:20px;font-style:italic;font-weight:500}
.card .sig{position:absolute;left:206px;top:128px;font-size:20px}
.acc{left:132px;width:936px;background:var(--white);border:1px solid #ddd;font-size:18px;color:#333}
.acc .label{position:absolute;left:44px;top:20px}
.acc .plus{position:absolute;right:34px;top:22px;width:20px;height:20px}
.partner{top:4190px;font-size:40px;font-weight:600;color:var(--brand);display:flex;align-items:center;gap:14px}
.partner i{display:block;width:44px;height:44px;border-radius:50%;background:var(--brand)}
.field{left:718px;width:356px;height:50px;background:var(--white);font-size:16px;color:#555;padding:14px 32px}
.foot-h{font-size:22px;color:#333}
.foot-item{display:flex;align-items:center;gap:24px;font-size:14.5px;line-height:26px;color:#333}
.social{display:flex;align-items:center;gap:22px;font-size:19px;color:#333}
.social i{display:block;width:40px;height:40px;border-radius:50%;border:2px solid var(--brand)}
.copyright{left:0;top:5094px;width:1200px;text-align:center;font-size:13px;color:#333}
</style>
</head>
<body>

<header class="abs site-header">
  <div class="abs brand"><span class="brand-mark"></span><span class="brand-name">AL-BAYAN<br><small style="font-size:11px;letter-spacing:4px">ARABIC ACADEMY</small></span></div>
  <nav class="abs nav"><span class="active">Home</span><span>About Us</span><span>Contact Us</span><span>Course Page</span><span>Our Courses</span></nav>
</header>

<section class="abs promo">
  <h1>Al Bayan</h1>
  <p>The Arabic Language Academy which helps understand Allah's words and the Noble Prophets teachings directly in the most Effective, Efficient and Effortless way. Never rely on translations again!</p>
  <div class="btn" style="left:846px;top:105px;width:262px;height:54px;font-size:21px">Start Learning Now</div>
</section>

<section class="abs hero" role="img" aria-label="City skyline with a sail-shaped tower by the sea at sunset">
  <div class="abs hero-title">Al Bayan</div>
  <div class="abs hero-sub">Neque porro quisquam est qui dolorem ipsum quia dolor sit amet, consectetur, adipisci velit</div>
  <div class="btn" style="left:494px;top:346px;width:208px;height:54px;font-size:21px">Get started</div>
  <svg class="abs arrow" style="left:58px" viewBox="0 0 30 30"><path d="M24 15H7M14 7l-8 8 8 8" fill="none" stroke="#fff" stroke-width="3"/></svg>
  <svg class="abs arrow" style="left:1108px" viewBox="0 0 30 30"><path d="M6 15h17M16 7l8 8-8 8" fill="none" stroke="#fff" stroke-width="3"/></svg>
  <div class="abs dots" style="left:572px;top:514px"><span></span><span></span><span style="background:var(--brand-light)"></span></div>
</section>

<div class="abs photo" style="left:90px;top:1020px;width:418px;height:456px" role="img" aria-label="Ornate holy book with prayer beads on a wooden table"></div>
<div class="abs feature" style="left:518px;top:1020px"><div class="icon"></div><h3>Efficient</h3><p>Lorem ipsum dolor sit amet, consectetur adipiscing elit, sed do</p></div>
<div class="abs feature" style="left:860px;top:1020px"><div class="icon"></div><h3>Effective</h3><p>Lorem ipsum dolor sit amet, consectetur adipiscing elit, sed</p></div>
<div class="abs feature" style="left:692px;top:1282px"><div class="icon"></div><h3>Effortless</h3><p>Lorem ipsum dolor sit amet, consectetur adipiscing elit, sed do</p></div>

<section class="abs band" style="top:1586px;height:374px" role="img" aria-label="Faint mosque skyline under a blue overlay">
  <div class="abs band-head" style="top:70px;font-size:22px;font-weight:500">7 LEARNING STRATEGIES THAT WILL BOOST YOUR ARABIC LEARNING INSTANTLY</div>
  <p class="abs band-head" style="left:180px;width:840px;top:124px;font-size:15px;line-height:36px">Lorem ipsum dolor sit amet, consectetur adipiscing elit, sed do eiusmod tempor incididunt ut labore et dolore magna aliqua. Quis ipsum suspendisse ultrices gravida. Risus commodo viverra maecenas accumsan lacus vel facilisis.</p>
  <div class="btn" style="left:496px;top:266px;width:208px;height:56px;font-size:21px">Book your spot</div>
</section>

<h2 class="abs section-title" style="top:2050px;color:var(--brand)">TESTIMONIAL</h2>
<div class="abs card" style="top:2134px;background:var(--panel)">
  <div class="avatar" role="img" aria-label="Student portrait"></div>
  <p class="quote">Neque porro quisquam est qui dolorem ipsum quia dolor sit amet, consectetur, adipisci velit..."There is no one who loves pain itself,</p>
  <div class="who">-Daniel</div>
  <div class="sig">Lorem ipsum dolor sit amet, <span style="color:var(--brand)">consectetur</span></div>
</div>
<div class="abs card" style="top:2330px;background:var(--brand);color:var(--white)">
  <div class="avatar" role="img" aria-label="Student portrait"></div>
  <p class="quote">Neque porro quisquam est qui dolorem ipsum quia dolor sit amet, consectetur, adipisci velit..."There is no one who loves pain itself,</p>
  <div class="who" style="top:86px">-Daniel</div>
  <div class="sig" style="top:124px;left:202px">Lorem ipsum dolor sit amet,</div>
</div>
<div class="abs dots" style="left:572px;top:2542px"><span style="background:var(--brand);width:12px;height:12px"></span><span style="background:var(--brand);width:12px;height:12px"></span><span style="background:var(--brand);width:12px;height:12px"></span></div>

<section class="abs band" style="top:2612px;height:384px" role="img" aria-label="Faint mosque skyline under a blue overlay">
  <h2 class="abs section-title" style="top:44px;color:var(--white)">ABOUT US</h2>
  <p class="abs band-head" style="left:190px;width:820px;top:120px;font-size:16px;line-height:37px">Neque porro quisquam est qui dolorem ipsum quia dolor sit amet, consectetur, adipisci velit..."There is no one who loves pain itself, who seeks after it and wants to have it, simply because it is pain..."ui dolorem ipsum quia dolor sit amet, consectetur, adipisci velit.</p>
</section>
<svg class="abs" style="left:158px;top:2876px" width="886" height="364" viewBox="0 0 886 364" role="img" aria-label="Video cover: domed mosque with minarets at sunset">
  <defs><linearGradient id="vid" x1="0" y1="0" x2="0" y2="1"><stop offset="0" stop-color="#8a8a92"/><stop offset=".45" stop-color="#c9874a"/><stop offset="1" stop-color="#2c2a2c"/></linearGradient></defs>
  <path d="M0 14 Q443 4 886 0 V348 Q443 352 0 364 Z" fill="url(#vid)"/>
  <circle cx="443" cy="178" r="33" fill="var(--accent)"/>
  <path d="M432 160 L458 178 L432 196 Z" fill="#fff"/>
</svg>

<section class="abs" style="left:90px;top:3346px;width:1020px;height:730px;background:var(--panel)">
  <h2 class="abs section-title" style="left:0;width:1020px;top:44px;color:#333">FEATURES</h2>
</section>
<div class="abs acc" style="top:3484px;height:68px"><span class="label">24/7 Access</span><svg class="plus" viewBox="0 0 20 20"><circle cx="10" cy="10" r="9" fill="#333"/><path d="M10 5v10M5 10h10" stroke="#fff" stroke-width="2"/></svg></div>
<div class="abs acc" style="top:3566px;height:68px"><span class="label">Learn at your own Pace</span><svg class="plus" viewBox="0 0 20 20"><circle cx="10" cy="10" r="9" fill="#333"/><path d="M10 5v10M5 10h10" stroke="#fff" stroke-width="2"/></svg></div>
<div class="abs acc" style="top:3652px;height:138px"><span class="label">Certificate</span><p style="position:absolute;left:44px;top:56px;width:800px;font-size:14.5px;line-height:32px;color:#555">Sed ut perspiciatis unde omnis iste natus error sit voluptatem accusantium doloremque laudantium, totam rem aperiam, eaque ipsa quae ab illo inventore</p></div>
<div class="abs acc" style="top:3814px;height:68px"><span class="label">Free Study Material</span><svg class="plus" viewBox="0 0 20 20"><circle cx="10" cy="10" r="9" fill="#333"/><path d="M10 5v10M5 10h10" stroke="#fff" stroke-width="2"/></svg></div>
<div class="abs acc" style="top:3900px;height:68px"><span class="label">Qualified Teachers</span><svg class="plus" viewBox="0 0 20 20"><circle cx="10" cy="10" r="9" fill="#333"/><path d="M10 5v10M5 10h10" stroke="#fff" stroke-width="2"/></svg></div>

<div class="abs partner" style="left:136px"><i></i>PostHive</div>
<div class="abs partner" style="left:508px"><i></i>MailWave</div>
<div class="abs partner" style="left:842px;font-size:32px"><i style="width:34px;height:34px"></i>FeedStream</div>

<section class="abs band" style="top:4316px;height:394px" role="img" aria-label="Faint mosque skyline under a blue overlay">
  <h2 class="abs" style="left:90px;top:84px;font-size:40px;font-weight:500;color:var(--white)">KEEP IN TOUCH</h2>
  <p class="abs" style="left:94px;top:146px;width:512px;font-size:15px;line-height:32px;color:var(--white);text-align:justify">Lorem ipsum dolor sit amet, consectetur adipiscing elit, sed do eiusmod tempor incididunt ut labore et dolore magna aliqua. Quis ipsum suspendisse ultrices gravida. Risus commodo viverra maecenas accumsan lacus vel facilisis. et dolore magna aliqua. Quis ipsum suspendisse ultrices gravida. Risus commodo viverra maecenas accumsan lacus vel facilisis.</p>
  <div class="abs field" style="top:86px">First Name</div>
  <div class="abs field" style="top:150px">Last Name</div>
  <div class="abs field" style="top:214px">Email</div>
  <div class="btn" style="left:718px;top:284px;width:356px;height:60px;font-size:22px">Join Today</div>
</section>

<footer>
  <h4 class="abs foot-h" style="left:140px;top:4766px;font-weight:400">Contact Us</h4>
  <div class="abs foot-item" style="left:138px;top:4836px"><svg width="18" height="24" viewBox="0 0 18 24"><path d="M9 0a9 9 0 0 0-9 9c0 7 9 15 9 15s9-8 9-15a9 9 0 0 0-9-9z" fill="#222"/><circle cx="9" cy="9" r="3.5" fill="#fff"/></svg><span>Neque porro quisquam est<br>ipsum quia dolor sit amet,</span></div>
  <div class="abs foot-item" style="left:138px;top:4897px"><svg width="18" height="18" viewBox="0 0 24 24"><path d="M6.6 10.8a15 15 0 0 0 6.6 6.6l2.2-2.2c.3-.3.7-.4 1-.2 1.1.4 2.3.6 3.6.6.6 0 1 .4 1 1V20c0 .6-.4 1-1 1A17 17 0 0 1 3 4c0-.6.4-1 1-1h3.5c.6 0 1 .4 1 1 0 1.3.2 2.5.6 3.6.1.3 0 .7-.2 1z" fill="#222"/></svg><span>Tel: +1 555 014 2277</span></div>
  <div class="abs foot-item" style="left:138px;top:4957px"><svg width="20" height="16" viewBox="0 0 20 16"><rect width="20" height="16" rx="2" fill="#222"/><path d="M1 2l9 7 9-7" fill="none" stroke="#fff" stroke-width="1.6"/></svg><span>Email: info@albayan-academy.com</span></div>

  <h4 class="abs foot-h" style="left:526px;top:4766px;font-weight:400">Social Media</h4>
  <div class="abs social" style="left:526px;top:4838px"><i></i>Circlebook</div>
  <div class="abs social" style="left:526px;top:4890px"><i></i>Chirper</div>
  <div class="abs social" style="left:526px;top:4944px"><i></i>ViewTube</div>
  <div class="abs social" style="left:526px;top:4998px"><i></i>WorkLink</div>

  <div class="abs" style="left:880px;top:4780px;width:160px;text-align:center">
    <div style="width:110px;height:110px;margin:0 auto;background:var(--brand)"></div>
    <div style="margin-top:60px;font-size:22px;font-weight:600;letter-spacing:4px;color:#333">AL-BAYAN</div>
    <div style="font-size:10px;letter-spacing:4px;color:#555;margin-top:4px">ARABIC ACADEMY</div>
  </div>

  <div class="abs copyright">© 2019 All Rights Reserved | Privacy Policy | Terms and Conditions | SiteMap</div>
</footer>

</body>
</html>
```